Web-Design  für naturwissenschaflich-philosophische Institution
Web-Design für naturwissenschaflich-philosophische Institution
Zielgruppe
Es handelt sich um eine naturwissenschaflich-philosophische Institution. Besucher sind neben Natur- und Geisteswissenschaftlern auch interessierte Laien.
Kernthema der Seite ist alles rund um das Thema Zahlen, allerdings unter einem naturwissenschaftlich, philosophischen Aspekt. Nach einer grundsätzlichen Erklärung (Leitartikel 'Wozu Formen führen') baut die Seite sich auf aus zahreichen Beispielen/Beiträgen aus den unterschiedlichsten Fachbereichen, die scheinbar keinerlei Bezug zueinander haben, wie Mathematik, Geometrie einerseits und der großen Literatur einschließlich historischer und religiöser Schriften andererseits. Immer aber gibt es einen Bezug zu fraktal wachsenden Dreiecken.
Die Artikel sind meist populärwissenschaftlich formuliert. Es handelt sich nicht um esoterische Inhalte, auch wenn der Domainname www.tafelgrund.de das evtl. vermuten ließe. Keine Berührung zu Spiritualität. Die Institution ist im Aufbau und hat durchaus den Anspruch, diese klassischen Themen modern aufzugreifen. Sie ist nicht verstaubt.
Aufgabenstellung
Geordneter, klarer, transparenter Aufbau. Übersichtlich und strukturiert, wie zB www.kvt.de Es sollten geometrische Proportionen eingehalten werden (wie Symmetrie, goldener Schnitt). Nicht zu viele verschiedene Stilelemente. Die Seite sollte einladend sein, ggf. ansprechendes Bild auf Startseite (mit Bezug zu Zahlen, Geoemetrie).
Die Startseite braucht nun im Header kein Logo mehr zu haben. Der Seitentitel sollte sein 'Das Gefüge der Linien'. Siehe Anhang 'Header Beispiel'
Als Menüpunkte benötigen wir neben Home, nur 'Beiträge', 'Buch', 'Kontakt' oder einfach nur die bekannten drei Striche. Der Link zum Impressum genügt im Footer. Rechts oben benötigt man ein Suchfeld.
Besonderheit: Man benötigt eine Art zweiten Header, der aus einer Zahlenreihe besteht. Die einzelnen Zahlen müssen später verlinkt sein auf Unterseiten. Siehe Muster im Anhang. Der User muss sie als Link erkennen können (evtl. Programmierthema: zB Hervorheben beim drüberhoovern). Die Zahlen müssen erweiterbar sein, ggf. über Pfeil klicken, siehe
Es gibt einen zentralen Startartikel. Auf diesen muss man leicht kommen. Im Muster heißt er 'Wozu die Formen führen'.
Das Bild hier ist sehr wichtig. Es sollte bestehn aus vielen interessanten Zahlen, wie in 'Zahlenwolke' angegeben. Und möglichst auch den Dreiecken wie in 'Logo1'.
Weiter unten auf der Startseite sollte es dann weitere Elemente geben, einmal wo man zu bestimmten Unterkategorien kommt, im Muster sind das 'Bibel und Zahlen' 'Naturwissenschaft' etc. und dann evtl weiter unten noch ein Stilelemente, in welchem man die neuesten Artikel verlinken kann.

```html
<!DOCTYPE html>
<html lang="de">
<head>
<meta charset="utf-8">
<title>Das Gefüge der Linien</title>
<link href="https://fonts.googleapis.com/css2?family=Poppins:wght@400;500;600;700&display=swap" rel="stylesheet">
<style>
  :root{
    --ink:#1f2d44;
    --accent:#1282f0;
    --band:#eeeeee;
    --card:#f1f1f1;
    --white:#ffffff;
    --hero-light:#5aa8e6;
    --hero-mid:#3a88d2;
    --hero-deep:#1b5aa0;
    --hero-night:#0f3f7a;
  }
  *{box-sizing:border-box;margin:0;padding:0}
  html,body{width:1153px;height:1200px;overflow:hidden;background:var(--white);
    font-family:"Poppins",sans-serif;color:var(--ink)}
  .site{position:relative;width:1153px;height:1200px}

  .topbar{position:absolute;top:0;left:0;width:100%;height:60px;background:var(--white);
    box-shadow:0 1px 3px rgba(0,0,0,.08)}
  .menu{position:absolute;left:521px;top:22px;display:flex;align-items:center;list-style:none;
    font-size:11px;font-weight:500;letter-spacing:.2px}
  .menu li{display:flex;align-items:center}
  .menu li+li::before{content:"";width:1px;height:9px;background:#c8c8c8;margin:0 12px}
  .menu a{color:var(--ink);text-decoration:none;padding-bottom:4px}
  .menu .active{color:var(--accent);border-bottom:2px solid var(--accent)}
  .search{position:absolute;left:865px;top:18px;width:120px;height:24px;border:1px solid #9aa3ae;
    border-radius:3px;display:flex;align-items:center;padding:0 5px}
  .search span{flex:1;font-size:10px;color:#d0d4d8}

  .numberbar{position:absolute;top:60px;left:0;width:100%;height:36px;background:var(--band)}
  .numbers{position:absolute;left:740px;top:9px;display:flex;align-items:center;gap:6px;list-style:none}
  .numbers .num{width:18px;height:18px;border-radius:3px;background:var(--ink);color:var(--white);
    font-size:13px;font-weight:600;display:flex;align-items:center;justify-content:center}
  .numbers .num.current{background:var(--accent)}
  .numbers .arrow{width:10px;height:18px;display:flex;align-items:center;justify-content:center}

  .hero{position:absolute;top:96px;left:0;width:100%;height:498px;overflow:hidden;
    background:
      radial-gradient(ellipse 55% 60% at 30% 90%, rgba(15,63,122,.75), transparent 70%),
      radial-gradient(ellipse 40% 45% at 88% 40%, rgba(15,63,122,.55), transparent 70%),
      radial-gradient(ellipse 45% 40% at 60% 15%, rgba(27,90,160,.6), transparent 70%),
      linear-gradient(120deg,var(--hero-mid) 0%,var(--hero-light) 45%,var(--hero-deep) 100%)}
  .hero-title{position:absolute;left:170px;top:152px;font-size:52px;line-height:59px;font-weight:700;
    color:var(--white);letter-spacing:-.5px;white-space:nowrap}
  .hero-button{position:absolute;left:170px;top:305px;width:219px;height:36px;background:var(--band);
    color:var(--ink);font-size:11px;font-weight:500;display:flex;align-items:center;justify-content:center}
  .hero-brand{position:absolute;left:658px;top:322px;font-size:41px;line-height:56px;font-weight:500;
    color:var(--white);letter-spacing:.5px}

  .cards{position:absolute;top:690px;left:170px;display:flex;gap:24px}
  .card{position:relative;width:256px;height:300px;background:var(--card);
    box-shadow:0 2px 5px rgba(0,0,0,.12);padding:23px 25px}
  .card h2{font-size:28.5px;line-height:33px;font-weight:600;height:90px;overflow-wrap:anywhere}
  .card p{font-size:10.6px;line-height:15.6px;color:#3a4658;margin-right:-8px}
  .card .more{position:absolute;left:25px;top:240px;width:134px;height:36px;background:var(--accent);
    color:var(--white);font-size:11px;font-weight:600;display:flex;align-items:center;justify-content:center}

  .to-top{position:absolute;left:1034px;top:1080px;width:36px;height:35px;background:var(--band);
    display:flex;align-items:center;justify-content:center}
  .footer{position:absolute;left:0;top:1138px;width:100%;height:62px;background:var(--band);
    box-shadow:0 -2px 4px rgba(0,0,0,.04)}
</style>
</head>
<body>
<div class="site">
  <header class="topbar">
    <ul class="menu">
      <li><a class="active" href="#">HOME</a></li>
      <li><a href="#">BETRAGE</a></li>
      <li><a href="#">BUCH</a></li>
      <li><a href="#">KONTAKT</a></li>
      <li><a href="#">IMPRESSUM</a></li>
    </ul>
    <div class="search">
      <span>Suche</span>
      <svg width="12" height="12" viewBox="0 0 12 12"><circle cx="7" cy="5" r="3.8" fill="none" stroke="#1f2d44" stroke-width="1.2"/><line x1="4.3" y1="7.7" x2="1" y2="11" stroke="#1f2d44" stroke-width="1.3"/></svg>
    </div>
  </header>

  <nav class="numberbar">
    <ul class="numbers">
      <li class="arrow"><svg width="6" height="7" viewBox="0 0 6 7"><path d="M6 0L0 3.5L6 7Z" fill="#1f2d44"/></svg></li>
      <li class="num current">1</li><li class="num">2</li><li class="num">3</li>
      <li class="num">4</li><li class="num">5</li><li class="num">6</li>
      <li class="num">7</li><li class="num">8</li><li class="num">9</li>
      <li class="arrow"><svg width="6" height="7" viewBox="0 0 6 7"><path d="M0 0L6 3.5L0 7Z" fill="#1282f0"/></svg></li>
    </ul>
  </nav>

  <section class="hero" role="img" aria-label="Blaue Zahlenwolke mit großen und kleinen Ziffern über einem feinen Raster">
    <h1 class="hero-title">Wozu die<br>Formen führen ...</h1>
    <div class="hero-button">Lern mehr</div>
    <div class="hero-brand">Tafelgrund.de</div>
  </section>

  <section class="cards">
    <article class="card">
      <h2>Bibel und Zahlen</h2>
      <p>Die Heilige Schrift ist ein Werk aus Zahlen. Ihre Verfasser haben die archetypischen Inhalte in wundersamer Art und Weise in der Bibel. Und so weiter und so fort</p>
      <div class="more">Lern mehr</div>
    </article>
    <article class="card">
      <h2>Naturwissens<br>chaft</h2>
      <p>Die Heilige Schrift ist ein Werk aus Zahlen. Ihre Verfasser haben die archetypischen Inhalte in wundersamer Art</p>
      <div class="more">Lern mehr</div>
    </article>
    <article class="card">
      <h2>Philosophie</h2>
      <p>Die Heilige Schrift ist ein Werk aus Zahlen. Ihre Verfasser haben die archetypischen Inhalte in wundersamer Art und Weise der Bibel. Und so weiter und so fort und vieles mehr das sehr schön eindrucksvoll ist</p>
      <div class="more">Lern mehr</div>
    </article>
  </section>

  <div class="to-top"><svg width="18" height="15" viewBox="0 0 18 15"><path d="M9 0L18 15H0Z" fill="#1f2d44"/></svg></div>
  <footer class="footer"></footer>
</div>
</body>
</html>
```